Velvet Riot Rising Line of Sparkling Wine & Spirits

Back info: Nora Beth Quill Owner 555-318-4402 1480 E. Harlow Ave, Bldg. 2, & 3, Lodi Ca. 95871
Sparkling Wines & Memorabilia www.velvetriotrising.com
Ok I have uploaded the winning design. The color that I am after is the Fushia, Raspberry, Red, Matte Satin Matalic Finish. With a 24 Karet Gold color Foil. The Bottle is on the top row and it's the 2nd Bottle in. That is the Color that I want. This is the style of font. Make sure that you put what we're advertising. Good Luck to you all. Warmest regards, Nora
21 & up UniSex
Sparkling Wine and Memorabilia
there listed up above.....

```html
<!DOCTYPE html>
<html lang="en">
<head>
<meta charset="utf-8">
<title>Velvet Riot Rising — Business Card</title>
<link rel="stylesheet" href="https://fonts.googleapis.com/css2?family=Cinzel:wght@400;700&family=Great+Vibes&family=Poppins:wght@300;400;700&display=swap">
<style>
  :root {
    --backdrop: #9b9b9b;
    --fuchsia: #e0167f;
    --fuchsia-light: #e8218c;
    --raspberry: #b80a5a;
    --ink: #0d0d0d;
    --card-black: #1b1b1b;
    --rose-text: #e31a6c;
    --gold: #c8934a;
    --gold-deep: #8a5a26;
  }
  * { margin: 0; padding: 0; box-sizing: border-box; }
  html, body {
    width: 1200px;
    height: 1000px;
    overflow: hidden;
    background: var(--backdrop);
  }
  .canvas { position: relative; width: 1200px; height: 1000px; }

  .card {
    position: absolute;
    left: 296px;
    width: 608px;
    height: 351px;
    border-radius: 26px;
    overflow: hidden;
  }

  /* Front */
  .card--front { top: 129px; }
  .front-pattern {
    position: absolute;
    inset: 0;
    background: radial-gradient(ellipse at 50% 50%, var(--fuchsia-light) 0%, #d61379 50%, var(--raspberry) 100%);
  }
  .front-mark {
    position: absolute;
    left: 0; right: 0;
    top: 0; bottom: 0;
    display: flex;
    flex-direction: column;
    align-items: center;
    justify-content: center;
    gap: 18px;
  }
  .front-mark__circle {
    width: 150px;
    height: 150px;
    border-radius: 50%;
    background: var(--ink);
  }
  .front-mark__name {
    font-family: "Cinzel", serif;
    font-weight: 700;
    font-size: 26px;
    letter-spacing: 1px;
    color: var(--ink);
  }

  /* Back */
  .card--back { top: 532px; background: var(--card-black); }
  .crest-area {
    position: absolute;
    left: 303px;
    top: 0;
    width: 305px;
    height: 351px;
    background: radial-gradient(ellipse at 75% 55%, #2a2218 0%, #211d19 45%, var(--card-black) 80%);
  }
  .crest-mark {
    position: absolute;
    left: 303px;
    top: 0;
    width: 305px;
    height: 351px;
  }
  .details {
    position: absolute;
    left: 27px;
    top: 0;
    width: 260px;
    height: 351px;
    text-align: center;
  }
  .brand-name {
    position: absolute;
    left: 0; right: 0;
    top: 48px;
    font-family: "Cinzel", serif;
    font-weight: 700;
    font-size: 27px;
    line-height: 34px;
    color: var(--gold);
    white-space: nowrap;
  }
  .brand-tagline {
    position: absolute;
    left: -10px; right: -10px;
    top: 102px;
    font-family: "Cinzel", serif;
    font-weight: 700;
    font-size: 9.5px;
    letter-spacing: 3px;
    color: var(--gold-deep);
    white-space: nowrap;
  }
  .person-name {
    position: absolute;
    left: -20px; right: -20px;
    top: 129px;
    font-family: "Great Vibes", cursive;
    font-weight: 400;
    font-size: 40px;
    line-height: 44px;
    color: var(--rose-text);
    white-space: nowrap;
  }
  .person-role {
    position: absolute;
    left: 0; right: 0;
    top: 176px;
    font-family: "Cinzel", serif;
    font-weight: 700;
    font-size: 13px;
    letter-spacing: 3px;
    color: var(--rose-text);
  }
  .contact {
    position: absolute;
    left: -20px; right: -20px;
    top: 203px;
    font-family: "Poppins", sans-serif;
    font-weight: 300;
    font-size: 14.5px;
    line-height: 18px;
    color: var(--rose-text);
    font-style: normal;
  }
  .website {
    position: absolute;
    left: 0; right: 0;
    top: 297px;
    font-family: "Poppins", sans-serif;
    font-size: 15px;
    line-height: 20px;
    color: var(--rose-text);
  }
  .website strong { font-weight: 700; }
  .website span { font-weight: 400; }
</style>
</head>
<body>
<main class="canvas">
  <section class="card card--front" aria-label="Business card front">
    <div class="front-pattern" role="img" aria-label="Fuchsia and raspberry damask pattern background"></div>
    <div class="front-mark">
      <div class="front-mark__circle"></div>
      <div class="front-mark__name">Velvet Riot Rising</div>
    </div>
  </section>

  <section class="card card--back" aria-label="Business card back">
    <div class="crest-area" role="img" aria-label="Large gold foil outline of the brand crest"></div>
    <svg class="crest-mark" viewBox="0 0 305 351" aria-hidden="true">
      <circle cx="190" cy="185" r="150" fill="none" stroke="#c8934a" stroke-width="1.5"/>
      <text x="190" y="191" text-anchor="middle" font-family="Cinzel, serif" font-weight="400" font-size="17" fill="#c8934a">Velvet Riot Rising</text>
    </svg>
    <div class="details">
      <h1 class="brand-name">Velvet Riot Rising</h1>
      <p class="brand-tagline">LINE OF SPARKLING WINE &amp; SPIRITS</p>
      <h2 class="person-name">Nora Beth Quill</h2>
      <p class="person-role">OWNER</p>
      <address class="contact">
        (555) 318-4402<br>
        1480 E. Harlow Ave,<br>
        Bldg. 2, &amp; 3, Lodi Ca. 95871
      </address>
      <p class="website"><strong>velvetriotrising</strong><span>.com</span></p>
    </div>
  </section>
</main>
</body>
</html>
```